Dane Warbeck Photography Business Card

I am looking for a simple, yet elegant business card for my photography business.

It is a short turn around project as the cards need to be printed within 48 hours. So the earlier you submit, the more likely you are to be chosen.

I am a professional portrait, sports and commercial photographer located in Brisbane, Australia. I am looking for a professional business card to distribute to professional clients. The card needs to be professional and easy to read. It must have my contact information as listed below.

Industry/Entity Type

Business

Contact Information for Business Card

Dane Warbeck Photography
www.danewarbeckphoto.com.au
dane@danewarbeckphoto.com.au
+61 437 582 906

Font styles to use
Serif
Sans Serif

Colors
ffc214
fece3e
fee18a

Requirements
Must have
• Must have contact information as above,
• Please use a similar colourscheme to the one provided in the logo upload.
Nice to have
• A very simple, design, happy to have some geometric shapes etc. Must look professional

```html
<!DOCTYPE html>
<html lang="en">
<head>
<meta charset="utf-8">
<title>Dane Warbeck Photography – Business Card</title>
<link rel="stylesheet" href="https://fonts.googleapis.com/css2?family=Roboto:wght@300;400&family=Roboto+Condensed:wght@700&display=swap">
<style>
  :root {
    --card-bg: #e6e7e9;
    --charcoal: #3a3a3c;
    --ink: #111111;
    --text-grey: #4a4a4c;
    --gold: #ffc214;
    --gold-soft: #fece3e;
    --gold-deep: #c98a1c;
  }
  * { margin: 0; padding: 0; box-sizing: border-box; }
  html, body {
    width: 1200px;
    height: 686px;
    overflow: hidden;
    background: var(--card-bg);
  }
  .card {
    position: relative;
    width: 1200px;
    height: 686px;
    background: var(--card-bg);
    overflow: hidden;
    font-family: "Roboto", Arial, sans-serif;
  }
  .card__shapes {
    position: absolute;
    inset: 0;
  }
  .shape-band { fill: var(--charcoal); }
  .shape-accent { fill: var(--gold-soft); }

  .brand-mark {
    position: absolute;
    left: 48px;
    top: 52px;
    width: 186px;
    height: 186px;
    border-radius: 50%;
    background: radial-gradient(circle at 35% 30%, var(--gold) 0%, var(--gold-deep) 100%);
  }
  .brand-name {
    position: absolute;
    left: 272px;
    top: 92px;
    color: var(--text-grey);
    font-weight: 300;
    line-height: 1;
  }
  .brand-name__main {
    display: block;
    font-size: 74px;
    letter-spacing: -1px;
  }
  .brand-name__sub {
    display: block;
    font-size: 38px;
    margin-top: 6px;
    margin-left: 3px;
  }

  .contact-name {
    position: absolute;
    right: 45px;
    top: 313px;
    text-align: right;
    line-height: 1;
  }
  .contact-name__main {
    display: block;
    font-family: "Roboto Condensed", "Arial Narrow", sans-serif;
    font-weight: 700;
    font-size: 54px;
    color: var(--ink);
    letter-spacing: 0.5px;
  }
  .contact-name__sub {
    display: block;
    font-weight: 300;
    font-size: 33px;
    color: var(--ink);
    margin-right: 45px;
    margin-top: -2px;
    letter-spacing: 0.5px;
  }

  .contact-line {
    position: absolute;
    display: flex;
    align-items: center;
    font-weight: 300;
    font-size: 33px;
    color: var(--ink);
    line-height: 1;
  }
  .contact-line svg { flex: none; fill: var(--charcoal); }
  .contact-line--phone { left: 838px; top: 420px; gap: 24px; }
  .contact-line--email { left: 572px; top: 481px; gap: 52px; }
  .contact-line--web { left: 572px; top: 530px; gap: 52px; }
</style>
</head>
<body>
<div class="card">
  <svg class="card__shapes" width="1200" height="686" viewBox="0 0 1200 686" aria-hidden="true">
    <polygon class="shape-band" points="0,328 1125,143 0,602"/>
    <polygon class="shape-accent" points="0,602 1125,143 0,624"/>
    <polygon class="shape-band" points="295,585 1200,662 1200,686 955,686"/>
  </svg>

  <div class="brand-mark" aria-hidden="true"></div>
  <div class="brand-name">
    <span class="brand-name__main">DANE WARBECK</span>
    <span class="brand-name__sub">PHOTOGRAPHY</span>
  </div>

  <div class="contact-name">
    <span class="contact-name__main">DANE WARBECK</span>
    <span class="contact-name__sub">PHOTOGRAPHY</span>
  </div>

  <div class="contact-line contact-line--phone">
    <svg width="34" height="34" viewBox="0 0 24 24" aria-hidden="true">
      <path d="M6.6 10.8a15.2 15.2 0 0 0 6.6 6.6l2.2-2.2a1 1 0 0 1 1-.25 11.4 11.4 0 0 0 3.6.57 1 1 0 0 1 1 1V20a1 1 0 0 1-1 1A17 17 0 0 1 3 4a1 1 0 0 1 1-1h3.5a1 1 0 0 1 1 1c0 1.25.2 2.45.57 3.57a1 1 0 0 1-.25 1z"/>
    </svg>
    <span>+61 437 582 906</span>
  </div>

  <div class="contact-line contact-line--email">
    <svg width="31" height="22" viewBox="0 0 31 22" aria-hidden="true">
      <rect x="0" y="0" width="31" height="22" rx="1"/>
      <polyline points="1,1 15.5,12 30,1" fill="none" stroke="#e6e7e9" stroke-width="2"/>
    </svg>
    <span>dane@danewarbeckphoto.com.au</span>
  </div>

  <div class="contact-line contact-line--web">
    <svg width="31" height="31" viewBox="0 0 31 31" aria-hidden="true">
      <circle cx="15.5" cy="15.5" r="15.5"/>
      <rect x="0" y="11" width="31" height="9" fill="#e6e7e9"/>
      <rect x="3" y="13" width="25" height="5" rx="1"/>
    </svg>
    <span>www.danewarbeckphoto.com.au</span>
  </div>
</div>
</body>
</html>
```